Business Card Design Project

Business Card
We are rebranding with a new logo
Industry/Entity Type
Business
Contact Information for Business Card
Dennis Morvale +61 487215963 dennis@quorv.com.au P.O. Box 872 Fernlow QLD 4309
Requirements
Must have
- Logo

```html
<!DOCTYPE html>
<html lang="en">
<head>
<meta charset="utf-8">
<title>Quorv International – Business Card</title>
<link href="https://fonts.googleapis.com/css2?family=Dancing+Script:wght@600&family=Roboto:wght@400;700&display=swap" rel="stylesheet">
<style>
  :root {
    --backdrop: #e4e4e4;
    --card-white: #f7f7f7;
    --card-white-shade: #ebebeb;
    --brand-navy: #1d2b3a;
    --panel-deep: #0a4a68;
    --panel-bright: #0a6f9c;
    --panel-text: #ffffff;
  }
  * { margin: 0; padding: 0; box-sizing: border-box; }
  html, body {
    width: 1200px;
    height: 576px;
    overflow: hidden;
    background: var(--backdrop);
  }
  .canvas {
    position: relative;
    width: 1200px;
    height: 576px;
  }
  .card {
    position: absolute;
    top: 138px;
    width: 484px;
    height: 294px;
    border-radius: 12px;
    overflow: hidden;
    background: linear-gradient(180deg, var(--card-white) 0%, var(--card-white-shade) 100%);
  }
  .card--front { left: 82px; }
  .card--back { left: 602px; width: 480px; height: 292px; }

  .wordmark {
    position: absolute;
    text-align: center;
    font-family: "Roboto", sans-serif;
    font-weight: 700;
    color: var(--brand-navy);
    letter-spacing: 3px;
    line-height: 1.15;
  }
  .wordmark__line--main { display: block; font-size: 40px; letter-spacing: 2px; }
  .wordmark__line--sub { display: block; font-size: 15px; letter-spacing: 3px; }
  .card--front .wordmark { left: 0; right: 0; top: 98px; }
  .card--back .wordmark { left: 290px; width: 170px; top: 98px; }

  .panel {
    position: absolute;
    left: 0; top: 0;
    width: 480px;
    height: 292px;
  }
  .holder {
    position: absolute;
    left: 22px;
    top: 36px;
    color: var(--panel-text);
  }
  .holder__name {
    font-family: "Dancing Script", cursive;
    font-weight: 600;
    font-size: 24px;
    line-height: 1;
  }
  .holder__role {
    font-family: "Roboto", sans-serif;
    font-size: 11.5px;
    margin-top: 6px;
  }
  .contacts {
    position: absolute;
    left: 24px;
    top: 213px;
    list-style: none;
    font-family: "Roboto", sans-serif;
    font-size: 12px;
    color: var(--panel-text);
  }
  .contacts__item {
    display: flex;
    align-items: center;
    height: 17px;
  }
  .contacts__icon {
    width: 11px;
    height: 11px;
    margin-right: 12px;
    fill: var(--panel-text);
  }
</style>
</head>
<body>
<main class="canvas">
  <section class="card card--front" aria-label="Card front">
    <div class="wordmark">
      <span class="wordmark__line--main">QUORV</span>
      <span class="wordmark__line--sub">INTERNATIONAL</span>
    </div>
  </section>

  <section class="card card--back" aria-label="Card back">
    <svg class="panel" viewBox="0 0 480 292" aria-hidden="true">
      <defs>
        <linearGradient id="panelFill" x1="0" y1="0" x2="1" y2="0">
          <stop offset="0" stop-color="var(--panel-deep)"/>
          <stop offset="1" stop-color="var(--panel-bright)"/>
        </linearGradient>
      </defs>
      <path d="M0 0 H278 Q214 146 278 292 H0 Z" fill="url(#panelFill)"/>
    </svg>

    <div class="holder">
      <div class="holder__name">Dennis Morvale</div>
      <div class="holder__role">Managing Director</div>
    </div>

    <ul class="contacts">
      <li class="contacts__item">
        <svg class="contacts__icon" viewBox="0 0 12 12"><path d="M1 4 Q6 0 11 4 L9.5 5.5 L8 4.5 V3.5 Q6 3 4 3.5 V4.5 L2.5 5.5 Z M3 6 H9 L10 11 H2 Z"/></svg>
        +61 487215963
      </li>
      <li class="contacts__item">
        <svg class="contacts__icon" viewBox="0 0 12 12"><path d="M0.5 2.5 H11.5 V9.5 H0.5 Z M1.5 3.2 L6 6.6 L10.5 3.2 V3 H1.5 Z" fill-rule="evenodd"/></svg>
        dennis@quorv.com.au
      </li>
      <li class="contacts__item">
        <svg class="contacts__icon" viewBox="0 0 12 12"><path d="M6 0.5 A4 4 0 0 1 10 4.5 C10 7.5 6 11.5 6 11.5 C6 11.5 2 7.5 2 4.5 A4 4 0 0 1 6 0.5 Z M6 3 A1.5 1.5 0 1 0 6 6 A1.5 1.5 0 1 0 6 3 Z" fill-rule="evenodd"/></svg>
        P.O. Box 872 Fernlow QLD 4309
      </li>
    </ul>

    <div class="wordmark">
      <span class="wordmark__line--main">QUORV</span>
      <span class="wordmark__line--sub">INTERNATIONAL</span>
    </div>
  </section>
</main>
</body>
</html>
```